I need a bag for flour with windows from the front ill attach some sample title is MAPLE CROFT MIXBAKE FLOUR
with color changing on the side stand up pouch I want to be able to put stickers ford different type of flour

Target Market(s)

retail store

Industry/Entity Type

flour retails

Font styles to use
Serif

Colors
0094D4
00A9DD
6FCCEA
C7EBF8
E9F6FB
00AB8E
00BBA5
67D7C9
C6EFE9
E9F9F6

Requirements
Must have
• creative
Nice to have
• I need a place so I can place the stickers of the flour
Should not have
• simple

```html
<!DOCTYPE html>
<html lang="en">
<head>
<meta charset="UTF-8">
<title>Maple Croft Mixbake Flour Pouch Range</title>
<link href="https://fonts.googleapis.com/css2?family=Playfair+Display:wght@400;900&family=Allura&family=Roboto:wght@400&display=swap" rel="stylesheet">
<style>
  :root {
    --panel-grey: #dcdcdc;
    --panel-blue: #3a9bc4;
    --panel-green: #249478;
    --panel-light: #eeeeee;
    --blue-deep: #0094d4;
    --blue: #00a9dd;
    --blue-mid: #6fccea;
    --blue-pale: #c7ebf8;
    --blue-mist: #e9f6fb;
    --teal-deep: #00ab8e;
    --teal: #00bba5;
    --teal-mid: #67d7c9;
    --teal-pale: #c6eff9;
    --teal-soft: #c6efe9;
    --teal-mist: #e9f9f6;
    --white: #ffffff;
    --flour-light: #eeeae0;
    --flour-shade: #d8d2c4;
    --ink-soft: rgba(0,0,0,0.35);
  }
  * { margin: 0; padding: 0; box-sizing: border-box; }
  html, body { width: 1200px; height: 574px; overflow: hidden; }
  body { position: relative; font-family: "Roboto", sans-serif; }

  .panel { position: absolute; top: 0; height: 574px; }
  .panel--grey { left: 0; width: 294px; background: var(--panel-grey); }
  .panel--blue { left: 294px; width: 294px; background: var(--panel-blue); }
  .panel--green { left: 588px; width: 307px; background: var(--panel-green); }
  .panel--light { left: 895px; width: 305px; background: var(--panel-light); }

  .pouch {
    position: absolute;
    width: 198px;
    height: 324px;
    background: var(--bag);
    border-radius: 3px;
    box-shadow: 0 8px 14px -6px var(--ink-soft);
    overflow: hidden;
  }
  .pouch__seal {
    position: absolute; left: 0; top: 0; width: 100%; height: 26px;
    background: repeating-linear-gradient(to bottom, var(--band) 0 3px, rgba(255,255,255,0.3) 3px 4px);
  }
  .pouch__window {
    position: absolute; left: 49px; top: 38px; width: 99px; height: 168px;
    background: radial-gradient(ellipse at 40% 40%, var(--flour-light), var(--flour-shade));
  }
  .pouch__title {
    position: absolute; left: 0; top: 212px; width: 100%;
    text-align: center; color: var(--cake);
  }
  .pouch__brand {
    display: block;
    font-family: "Playfair Display", serif;
    font-weight: 400; font-size: 10px; line-height: 13px;
    letter-spacing: 3px;
  }
  .pouch__product {
    display: block;
    font-family: "Playfair Display", serif;
    font-weight: 900; font-size: 32px; line-height: 34px;
    letter-spacing: 1px;
  }
  .pouch__flour {
    display: block;
    font-family: "Allura", cursive;
    font-size: 36px; line-height: 30px;
    color: var(--flour);
    margin: -6px 0 0 40px;
  }
  .pouch__sticker {
    position: absolute; left: 59px; top: 285px; width: 80px; height: 16px;
    border: 1px dashed var(--cake);
    border-radius: 8px;
    opacity: 0.7;
  }
  .pouch__weight {
    position: absolute; left: 0; bottom: 8px; width: 100%;
    text-align: center; font-size: 7px; color: var(--weight);
  }

  .pouch--blue { left: 47px; top: 86px; --bag: var(--blue); --band: var(--blue-mist); --cake: var(--white); --flour: var(--blue-pale); --weight: var(--white); }
  .pouch--mist { left: 352px; top: 156px; --bag: var(--blue-mist); --band: var(--blue-deep); --cake: var(--blue-deep); --flour: var(--teal); --weight: var(--blue-deep); }
  .pouch--teal { left: 650px; top: 86px; --bag: var(--teal-deep); --band: var(--teal-mid); --cake: var(--white); --flour: var(--teal-soft); --weight: var(--white); }
  .pouch--mint { left: 935px; top: 151px; --bag: var(--teal-mist); --band: var(--teal-mid); --cake: var(--teal-deep); --flour: var(--teal); --weight: var(--teal-deep); }
</style>
</head>
<body>
  <div class="panel panel--grey"></div>
  <div class="panel panel--blue"></div>
  <div class="panel panel--green"></div>
  <div class="panel panel--light"></div>

  <div class="pouch pouch--blue">
    <div class="pouch__seal"></div>
    <div class="pouch__window" role="img" aria-label="Clear window showing the white flour inside"></div>
    <div class="pouch__title"><span class="pouch__brand">MAPLE CROFT</span><span class="pouch__product">MIXBAKE</span><span class="pouch__flour">Flour</span></div>
    <div class="pouch__sticker" aria-label="Space for flour type sticker"></div>
    <div class="pouch__weight">500g</div>
  </div>

  <div class="pouch pouch--mist">
    <div class="pouch__seal"></div>
    <div class="pouch__window" role="img" aria-label="Clear window showing the white flour inside"></div>
    <div class="pouch__title"><span class="pouch__brand">MAPLE CROFT</span><span class="pouch__product">MIXBAKE</span><span class="pouch__flour">Flour</span></div>
    <div class="pouch__sticker" aria-label="Space for flour type sticker"></div>
    <div class="pouch__weight">500g</div>
  </div>

  <div class="pouch pouch--teal">
    <div class="pouch__seal"></div>
    <div class="pouch__window" role="img" aria-label="Clear window showing the white flour inside"></div>
    <div class="pouch__title"><span class="pouch__brand">MAPLE CROFT</span><span class="pouch__product">MIXBAKE</span><span class="pouch__flour">Flour</span></div>
    <div class="pouch__sticker" aria-label="Space for flour type sticker"></div>
    <div class="pouch__weight">500g</div>
  </div>

  <div class="pouch pouch--mint">
    <div class="pouch__seal"></div>
    <div class="pouch__window" role="img" aria-label="Clear window showing the white flour inside"></div>
    <div class="pouch__title"><span class="pouch__brand">MAPLE CROFT</span><span class="pouch__product">MIXBAKE</span><span class="pouch__flour">Flour</span></div>
    <div class="pouch__sticker" aria-label="Space for flour type sticker"></div>
    <div class="pouch__weight">500g</div>
  </div>
</body>
</html>
```